i need a business card for a plumbing company in california

we are a drain cleaning , maintenance plumbing company who is starting new marketing campaign for a tatrench-less pipe installation department .

Target Market(s)

the professional who appreciates time and quality workmanship.

Industry/Entity Type

Plumbing

Colors
0655a3
ec1f27

Requirements
Must have
• the second logo needs to be included
Nice to have
• a focus on the services offered
Should not have
• any underlined words on the brief

```html
<!DOCTYPE html>
<html lang="en">
<head>
<meta charset="utf-8">
<title>Delta Drainworks – Business Card</title>
<link rel="stylesheet" href="https://fonts.googleapis.com/css2?family=Arimo:wght@400;700&display=swap">
<style>
  :root {
    --backdrop: #676767;
    --card-white: #ffffff;
    --brand-red: #e0252b;
    --brand-red-light: #e5393e;
    --logo-grey: #7b7b70;
    --text-dark: #3a3a3a;
    --divider: #bdbdbd;
  }
  * { margin: 0; padding: 0; box-sizing: border-box; }
  html, body {
    width: 1200px;
    height: 802px;
    overflow: hidden;
    background: var(--backdrop);
    font-family: "Arimo", Arial, sans-serif;
  }
  .canvas { position: relative; width: 1200px; height: 802px; }
  .card {
    position: absolute;
    top: 274px;
    width: 442px;
    height: 265px;
  }
  .card-front { left: 136px; background: var(--card-white); }
  .card-back { left: 624px; background: var(--brand-red); overflow: hidden; }

  .brand-name {
    position: absolute;
    left: 28px;
    top: 104px;
    font-weight: 700;
    font-size: 25px;
    line-height: 27px;
    color: var(--logo-grey);
    text-align: right;
    width: 180px;
  }
  .divider {
    position: absolute;
    left: 226px;
    top: 62px;
    width: 1px;
    height: 117px;
    background: var(--divider);
  }
  .contact-block {
    position: absolute;
    left: 247px;
    top: 68px;
    color: var(--text-dark);
    font-size: 12.8px;
  }
  .person-name {
    color: var(--brand-red);
    font-weight: 700;
    font-size: 15px;
    line-height: 16px;
    letter-spacing: 0.2px;
  }
  .person-title { font-size: 12.8px; line-height: 15px; margin-bottom: 6px; }
  .contact-list { list-style: none; }
  .contact-list li {
    display: flex;
    align-items: center;
    gap: 5px;
    line-height: 15.8px;
  }
  .contact-list svg { width: 9px; height: 9px; fill: var(--brand-red); flex: none; }
  .address { margin-top: 5px; line-height: 15.8px; }

  .pattern-field {
    position: absolute;
    inset: 0;
    background: linear-gradient(135deg, var(--brand-red-light), var(--brand-red));
  }
  .back-name {
    position: absolute;
    left: 300px;
    top: 140px;
    color: var(--card-white);
    font-weight: 700;
    font-size: 17px;
    line-height: 19px;
  }
</style>
</head>
<body>
<div class="canvas">
  <section class="card card-front">
    <div class="brand-name">Delta<br>Drainworks</div>
    <div class="divider"></div>
    <div class="contact-block">
      <div class="person-name">JONATHAN SMITH</div>
      <div class="person-title">Managing Director</div>
      <ul class="contact-list">
        <li><svg viewBox="0 0 10 10"><path d="M0 3.5Q5 0 10 3.5L8.5 5 7 4V3H3v1L1.5 5Z M2 6h6l1 4H1Z"/></svg>044-123 456 789</li>
        <li><svg viewBox="0 0 10 10"><path d="M2.5 0h5v10h-5Z M3.5 1v7h3V1Z" fill-rule="evenodd"/></svg>044-123 456 789</li>
        <li><svg viewBox="0 0 10 10"><path d="M0 2h10v6H0Z M1 3l4 3 4-3" /></svg>info@deltadrain.com</li>
        <li><svg viewBox="0 0 10 10"><circle cx="5" cy="5" r="5"/></svg>www.deltadrain.com</li>
      </ul>
      <p class="address">12345, Address Goes Here<br>Country Name, 123456.</p>
    </div>
  </section>

  <section class="card card-back">
    <div class="pattern-field" role="img" aria-label="Faint repeating brand-mark pattern on red"></div>
    <div class="back-name">Delta<br>Drainworks</div>
  </section>
</div>
</body>
</html>
```